Verlindo Magician

I want the business card for my business to give to people who watch that later I will be employed to show magic here is my website http://www.verlindoillusions.example/I want the interesting design , i am very opened for formal and informal, I watch a lot of design so don't stick to the common shape and form but i hope it can also be produced the thing to write on will be the same as in picture that i will upload , i also will upload the logo for you that so can be easy to useDenis CostilleMagicianMAGICIAN BALSAMO 17 rue des Tilleuls - 25000 BESANÇON contact@verlindoillusions.example tel. 0381 946 157 tel. 0674 219 503

```html
<!DOCTYPE html>
<html lang="fr">
<head>
<meta charset="utf-8">
<title>Verlindo Magician – Business Card</title>
<link href="https://fonts.googleapis.com/css2?family=Jost:wght@400;500&display=swap" rel="stylesheet">
<style>
  :root {
    --backdrop: #3a3837;
    --card-black: #242424;
    --card-white: #efefef;
    --frame-white: #ffffff;
    --accent-red: #e8262b;
    --ink: #111111;
    --text-light: #f2f2f2;
  }
  * { box-sizing: border-box; margin: 0; padding: 0; }
  html, body { width: 1200px; height: 800px; overflow: hidden; }
  body {
    background: var(--backdrop);
    font-family: "Jost", "Futura", sans-serif;
    display: flex;
    align-items: center;
    justify-content: center;
    gap: 60px;
  }
  .card {
    width: 340px;
    height: 580px;
    position: relative;
  }
  /* Back: contact side */
  .card--contact {
    background: var(--card-black);
    border: 13px solid var(--frame-white);
    color: var(--text-light);
    display: flex;
    flex-direction: column;
    align-items: center;
    justify-content: center;
    text-align: center;
  }
  .suits { display: flex; gap: 8px; }
  .suits svg { width: 22px; height: 22px; fill: var(--text-light); }
  .suits--top { margin-bottom: 20px; }
  .suits--bottom { margin-top: 26px; }
  .contact__name {
    color: var(--accent-red);
    font-size: 27px;
    font-weight: 500;
    letter-spacing: 0.5px;
    text-transform: uppercase;
    line-height: 1;
  }
  .contact__role { font-size: 15px; margin-top: 4px; }
  .divider {
    width: 34px;
    height: 1px;
    background: var(--accent-red);
    margin: 16px 0;
  }
  .contact__details { font-size: 13px; line-height: 1.35; }
  .contact__address { font-size: 12.5px; }

  /* Front: brand side */
  .card--brand {
    background: var(--card-white);
    border: 11px solid var(--accent-red);
    display: flex;
    flex-direction: column;
    align-items: center;
    padding-top: 80px;
  }
  .brand__illustration { display: block; }
  .brand__name {
    margin-top: 14px;
    font-size: 50px;
    font-weight: 400;
    letter-spacing: 1px;
    color: var(--ink);
    line-height: 1;
  }
  .brand__tagline {
    margin-top: 4px;
    font-size: 14px;
    letter-spacing: 1px;
    color: var(--ink);
  }
</style>
</head>
<body>

  <section class="card card--contact" aria-label="Contact side">
    <div class="suits suits--top">
      <svg viewBox="0 0 24 24" aria-hidden="true"><path d="M12 2C9 6 3 9 3 14a4.5 4.5 0 0 0 8 2.8L9.5 22h5L13 16.8A4.5 4.5 0 0 0 21 14c0-5-6-8-9-12z"/></svg>
      <svg viewBox="0 0 24 24" aria-hidden="true"><path d="M12 1l8 11-8 11-8-11z"/></svg>
    </div>
    <h1 class="contact__name">Marc Ravoulet</h1>
    <p class="contact__role">Magician</p>
    <span class="divider"></span>
    <p class="contact__details">
      P: 0381 946 157<br>
      F: 0674 219 503<br>
      E: contact@verlindoillusions.example<br>
      www.verlindoillusions.example
    </p>
    <span class="divider"></span>
    <p class="contact__address">17 rue des Tilleuls - 25000 BESANÇON</p>
    <div class="suits suits--bottom">
      <svg viewBox="0 0 24 24" aria-hidden="true"><path d="M12 21.5C5 16 2 12.5 2 8.5A5 5 0 0 1 12 6a5 5 0 0 1 10 2.5c0 4-3 7.5-10 13z"/></svg>
      <svg viewBox="0 0 24 24" aria-hidden="true"><circle cx="12" cy="6.5" r="4.5"/><circle cx="6" cy="13" r="4.5"/><circle cx="18" cy="13" r="4.5"/><path d="M11 12h2l1.5 10h-5z"/></svg>
    </div>
  </section>

  <section class="card card--brand" aria-label="Brand side">
    <svg class="brand__illustration" width="240" height="300" viewBox="0 0 240 300" role="img" aria-label="Black ink illustration of the magician holding a playing card">
      <defs>
        <linearGradient id="illustration-tone" x1="0" y1="0" x2="0" y2="1">
          <stop offset="0" stop-color="#2a2a2a"/>
          <stop offset="1" stop-color="#0d0d0d"/>
        </linearGradient>
      </defs>
      <rect width="240" height="300" fill="url(#illustration-tone)"/>
    </svg>
    <p class="brand__name">VERLINDO</p>
    <p class="brand__tagline">MAGICIEN</p>
  </section>

</body>
</html>
```